Business Card for Professional Photographer

I'm looking for an eye catching modern clean design that compliments my logo/ website fonts & colours.
I specialise in architecture, corporate & commercial photography so I'm marketing to professional clients rather than portrait / wedding clients.

I would prefer to not have a solid black design.

My logo brand guide is as follows :

Main front font. : Reislust
Main font colour : #fff
Slogan front font : Ubuntu Bold
Monogram front font : Venti Medium
Container colour : #fff

I need print ready files in pdf .png & .eps formats.

Included in the files below are some screen grabs as reference to font & colours etc.

```html
<!DOCTYPE html>
<html lang="en">
<head>
<meta charset="utf-8">
<title>Clear Line Studio – Business Card</title>
<link href="https://fonts.googleapis.com/css2?family=Ubuntu:wght@300;400;500&display=swap" rel="stylesheet">
<style>
  :root {
    --backdrop: #2a2a2c;
    --card: #ffffff;
    --ink-grey: #6b6b6d;
    --ink-dark: #4a4a4c;
    --gold: #c9954b;
    --gold-light: #ecd08a;
    --gold-deep: #b9862f;
  }
  * { margin: 0; padding: 0; box-sizing: border-box; }
  html, body {
    width: 1200px; height: 874px; overflow: hidden;
    background: var(--backdrop);
    font-family: "Ubuntu", sans-serif;
  }
  .canvas {
    position: relative; width: 1200px; height: 874px;
    display: flex; flex-direction: column; align-items: center; justify-content: center; gap: 44px;
  }
  .card {
    position: relative; width: 660px; height: 377px;
    background: var(--card); border-radius: 22px;
    box-shadow: 0 10px 24px rgba(0,0,0,.35);
    overflow: hidden;
  }
  /* front */
  .front .lockup {
    position: absolute; left: 50%; top: 50%; transform: translate(-50%, -50%);
    display: flex; align-items: center; gap: 22px;
  }
  .lockup-mark { width: 70px; height: 70px; }
  .wordmark {
    font-weight: 300; color: var(--ink-grey); letter-spacing: .16em;
    text-transform: uppercase; line-height: 1;
  }
  .front .wordmark { font-size: 30px; }
  .tagline {
    display: block; font-weight: 500; color: var(--ink-grey);
    letter-spacing: .14em; font-size: 9px; margin-top: 7px;
  }
  /* back */
  .back .details { position: absolute; left: 48px; top: 40px; }
  .back .wordmark { font-size: 23px; }
  .back .tagline { font-size: 7.5px; margin-top: 5px; }
  .person-name { margin-top: 20px; font-size: 24px; font-weight: 500; color: var(--gold); }
  .person-role { font-size: 15px; color: var(--ink-grey); font-weight: 400; margin-top: 2px; }
  .address { margin-top: 18px; font-size: 15px; color: var(--ink-dark); line-height: 1.3; }
  .contacts { list-style: none; margin-top: 14px; font-size: 15px; color: var(--ink-dark); line-height: 1.4; }
  .contacts li { display: flex; align-items: center; gap: 9px; }
  .contacts svg { width: 11px; height: 11px; fill: var(--gold); flex: none; }
  .back .decor { position: absolute; right: 40px; top: 110px; width: 240px; height: 240px; }
</style>
</head>
<body>
<main class="canvas">
  <section class="card front" aria-label="Card front">
    <div class="lockup">
      <svg class="lockup-mark" viewBox="0 0 70 70" aria-hidden="true">
        <defs>
          <linearGradient id="goldSmall" x1="0" y1="0" x2="1" y2="1">
            <stop offset="0" stop-color="var(--gold-deep)"/>
            <stop offset=".6" stop-color="var(--gold-light)"/>
            <stop offset="1" stop-color="var(--gold)"/>
          </linearGradient>
        </defs>
        <circle cx="35" cy="35" r="30" fill="none" stroke="url(#goldSmall)" stroke-width="5"/>
      </svg>
      <div class="wordmark">Clear Line Studio
        <span class="tagline">Architecture Corporate Commercial</span>
      </div>
    </div>
  </section>

  <section class="card back" aria-label="Card back">
    <div class="details">
      <div class="wordmark">Clear Line Studio
        <span class="tagline">Architecture Corporate Commercial</span>
      </div>
      <p class="person-name">Daniel Hart</p>
      <p class="person-role">President</p>
      <p class="address">4120 Birchwood Drive<br>Fairbanks, Alaska 99701</p>
      <ul class="contacts">
        <li><svg viewBox="0 0 12 12"><path d="M2.5 1l2 2.5-1 1.2a7 7 0 0 0 3.8 3.8l1.2-1 2.5 2-1 1.5C5.5 11 1 6.5 1 2z"/></svg>555-201-4830</li>
        <li><svg viewBox="0 0 12 12"><path d="M3 0h6v12H3zM4 1.5v8h4v-8z"/></svg>555-318-7246</li>
        <li><svg viewBox="0 0 12 12"><path d="M3 1h6v3H3zM1 5h10v5H1zM3 8h6v4H3z"/></svg>555-427-9153</li>
        <li><svg viewBox="0 0 12 12"><path d="M0 2h12v8H0zM1 3l5 4 5-4z" fill-rule="evenodd"/></svg>hello@clearlinestudio.com</li>
        <li><svg viewBox="0 0 12 12"><circle cx="6" cy="6" r="5.5"/></svg>www.clearlinestudio.com</li>
      </ul>
    </div>
    <svg class="decor" viewBox="0 0 240 240" aria-hidden="true">
      <defs>
        <linearGradient id="goldLarge" x1="0" y1="0" x2="1" y2="1">
          <stop offset="0" stop-color="var(--gold-deep)"/>
          <stop offset=".55" stop-color="var(--gold-light)"/>
          <stop offset="1" stop-color="var(--gold)"/>
        </linearGradient>
      </defs>
      <circle cx="120" cy="120" r="108" fill="none" stroke="url(#goldLarge)" stroke-width="12"/>
    </svg>
  </section>
</main>
</body>
</html>
```